High end Electrical/home automation Business Card

Need a card for a high end electrical and home automation company utilising the existing logo.
Phone
Email
Website

Like black look with raised detail. Don’t necessarily need to keep colour of logo it could be made grayscale or white etc

Target Market(s)

High end clients

Contact Information for Business Card

Brightmoor Electrical

Requirements
Must have
• Logo, phone, email, website, address

High end look
Nice to have
• Black background card
Raised font
Should not have
• Lots of colour

```html
<!DOCTYPE html>
<html lang="en">
<head>
<meta charset="utf-8">
<title>Brightmoor Electrical – Business Card</title>
<link href="https://fonts.googleapis.com/css2?family=Lato:wght@400;700;900&display=swap" rel="stylesheet">
<style>
  :root {
    --backdrop: #d9d9d9;
    --card-black: #121314;
    --card-black-soft: #1c1d1f;
    --brand-blue: #0a88d8;
    --ink-white: #f2f2f4;
    --ink-dark: #101820;
    --edge-silver: #b9bcc0;
  }
  * { box-sizing: border-box; margin: 0; padding: 0; }
  html, body {
    width: 1200px; height: 800px; overflow: hidden;
    background: var(--backdrop);
    font-family: "Lato", Arial, sans-serif;
  }
  .canvas {
    position: relative; width: 1200px; height: 800px;
    display: flex; align-items: center; justify-content: center; gap: 40px;
  }
  .card {
    position: relative; width: 540px; height: 309px; overflow: hidden;
    box-shadow: 0 14px 30px rgba(0,0,0,0.28);
  }
  /* Front */
  .card-front { background: var(--brand-blue); }
  .front-shape { position: absolute; inset: 0; width: 100%; height: 100%; }
  .front-brand {
    position: absolute; left: 32px; bottom: 64px;
    display: flex; align-items: center; gap: 10px;
    color: var(--ink-white); font-weight: 900; font-size: 25px; letter-spacing: -0.3px;
  }
  .brand-dot {
    width: 16px; height: 16px; border-radius: 50%; background: var(--brand-blue);
  }
  .holder {
    position: absolute; right: 28px; top: 30px; text-align: right;
  }
  .holder-name {
    font-weight: 900; font-size: 22px; letter-spacing: 1px;
    color: var(--ink-dark); text-transform: uppercase;
  }
  .holder-title {
    font-weight: 700; font-size: 14px; color: var(--ink-white); margin-top: 1px;
  }
  .address, .contact {
    position: absolute; right: 28px; text-align: right;
    color: var(--ink-white); font-size: 12.5px; line-height: 1.35;
  }
  .address { top: 118px; }
  .contact { top: 190px; }
  .contact li { list-style: none; display: flex; justify-content: flex-end; align-items: center; gap: 7px; }
  .contact svg { width: 11px; height: 11px; fill: var(--ink-dark); }
  /* Back */
  .card-back { background: var(--card-black); }
  .back-brand {
    position: absolute; left: 34px; bottom: 54px;
    color: var(--ink-white); font-weight: 900; font-size: 34px; letter-spacing: -0.5px;
  }
  .back-web {
    position: absolute; left: 36px; bottom: 32px;
    color: var(--ink-white); font-size: 11px; letter-spacing: 4px;
  }
</style>
</head>
<body>
<main class="canvas">

  <section class="card card-front" aria-label="Card front">
    <svg class="front-shape" viewBox="0 0 540 309" preserveAspectRatio="none" aria-hidden="true">
      <path d="M0 0 H150 C235 10 280 60 290 130 C298 200 280 260 255 309 H0 Z" fill="var(--card-black-soft)"/>
      <path d="M150 0 C235 10 280 60 290 130 C298 200 280 260 255 309" fill="none" stroke="var(--edge-silver)" stroke-width="1.5"/>
    </svg>
    <div class="front-brand"><span class="brand-dot"></span>Brightmoor Electrical</div>

    <div class="holder">
      <p class="holder-name">Daniel Hartwell</p>
      <p class="holder-title">President</p>
    </div>

    <address class="address" style="font-style:normal">
      Brightmoor Electrical LLC<br>
      4120 Larkspur Road<br>
      Fairview, Alaska 99012
    </address>

    <ul class="contact">
      <li>555-014-2287
        <svg viewBox="0 0 24 24" aria-hidden="true"><path d="M6.6 10.8a15 15 0 0 0 6.6 6.6l2.2-2.2a1 1 0 0 1 1-.25 11.4 11.4 0 0 0 3.6.57 1 1 0 0 1 1 1V20a1 1 0 0 1-1 1A17 17 0 0 1 3 4a1 1 0 0 1 1-1h3.5a1 1 0 0 1 1 1c0 1.25.2 2.45.57 3.57a1 1 0 0 1-.25 1z"/></svg>
      </li>
      <li>info@brightmoorelectrical.com
        <svg viewBox="0 0 24 24" aria-hidden="true"><path d="M2 5h20v14H2z M2 5l10 8 10-8" stroke="var(--brand-blue)" stroke-width="1.5"/></svg>
      </li>
      <li>www.brightmoorelectrical.com
        <svg viewBox="0 0 24 24" aria-hidden="true"><circle cx="12" cy="12" r="10"/></svg>
      </li>
    </ul>
  </section>

  <section class="card card-back" aria-label="Card back">
    <p class="back-brand">Brightmoor Electrical</p>
    <p class="back-web">www.brightmoorelectrical.com</p>
  </section>

</main>
</body>
</html>
```